Interior Design/ New Construction interior finishes

Interior Design Website

Target Market(s)

Home builders, New Construction, Renovations, Public

Industry/Entity Type

Construction

Coding

Coded - Design and coding required

Number of Pages Required

1 page

Font styles to use
Sans Serif

Colors

Designer to choose colors to be used in the design.

Requirements
Must have
• Section to upload pictures of projects
• Simple and modern design
• Designer 1 details about myself
• Logo
• Upload section for photos for future jobs
Nice to have
• Sections they can click on to see certain rooms in a house
• Decorating, floral arrangements, holiday decorating.
• I have lots of before and after as well. Maybe a section for those.

```html
<!DOCTYPE html>
<html lang="en">
<head>
<meta charset="utf-8">
<title>Ridgeline Interiors</title>
<link href="https://fonts.googleapis.com/css2?family=Josefin+Sans:wght@400;600&family=Lato:wght@400;700&display=swap" rel="stylesheet">
<style>
:root{
  --orange:#e07a1f;
  --green:#3fa63c;
  --blue:#3a9acb;
  --dark:#222;
  --text:#555;
  --muted:#888;
  --line:#ddd;
  --white:#fff;
  --photo-warm:linear-gradient(135deg,#b7a792,#6e5c4a);
  --photo-cool:linear-gradient(135deg,#c9cdd1,#7c8289);
}
*{box-sizing:border-box;margin:0;padding:0}
html,body{width:1200px;height:4534px;overflow:hidden}
body{font-family:'Lato',sans-serif;color:var(--text);background:var(--white);position:relative}
.abs{position:absolute}
h2{font-family:'Josefin Sans',sans-serif;font-weight:400;color:var(--dark);font-size:38px;text-align:center}
.photo{background:var(--photo-cool)}
.photo.warm{background:var(--photo-warm)}

/* header */
.site-header{position:absolute;top:0;left:0;width:1200px;height:100px;background:var(--white);z-index:2}
.brand{position:absolute;left:98px;top:8px;display:flex;align-items:center;gap:10px}
.brand-dot{width:26px;height:26px;border-radius:50%;background:var(--dark)}
.brand-name{font-family:'Lato',sans-serif;font-weight:700;font-size:24px;color:var(--dark)}
.topbar{position:absolute;right:96px;top:18px;font-size:14px;color:var(--dark);display:flex;gap:26px;align-items:center}
.topbar span{display:flex;align-items:center;gap:8px}
.nav{position:absolute;right:96px;top:62px;display:flex;gap:30px;font-size:16px;color:var(--dark);align-items:center}
.nav .active{color:var(--orange)}

/* hero */
.hero{position:absolute;top:100px;left:0;width:1200px;height:505px}
.hero-band{position:absolute;left:0;top:181px;width:720px;height:128px;background:rgba(20,20,20,.6);color:var(--white);padding:18px 0 0 100px}
.hero-band h1{font-family:'Josefin Sans',sans-serif;font-weight:400;font-size:52px}
.hero-band p{font-size:22px;margin-top:4px}
.dots{position:absolute;left:568px;top:443px;display:flex;gap:6px}
.dots i{width:12px;height:12px;border-radius:50%;border:2px solid var(--white)}
.dots i:first-child{background:var(--white)}

/* welcome */
.welcome-title{top:685px;left:0;width:1200px}
.welcome-text{top:756px;left:210px;width:780px;font-size:14px;line-height:24px;text-align:center;color:var(--muted)}
.services{top:846px;left:100px;width:998px;height:578px;display:grid;grid-template-columns:repeat(3,1fr);grid-template-rows:repeat(2,1fr)}
.tile{color:var(--white);text-align:center;padding:30px 34px 0}
.tile h3{font-family:'Josefin Sans',sans-serif;font-weight:400;font-size:24px;margin:14px 0 12px}
.tile p{font-size:13px;line-height:21px}
.tile.orange{background:var(--orange)}
.tile.green{background:var(--green)}
.tile.blue{background:var(--blue)}

/* before after */
.ba{top:1522px;left:0;width:1200px;height:524px;background:linear-gradient(#6b6b6b,#3e3e3e)}
.ba-frame{position:absolute;top:78px;left:100px;width:1000px;height:364px;border:4px solid var(--white);display:flex;gap:4px;background:var(--white)}
.ba-frame .photo{flex:1;position:relative}
.ba-label{position:absolute;bottom:0;left:0;right:0;height:44px;background:rgba(30,30,30,.6);color:var(--white);font-family:'Josefin Sans',sans-serif;font-size:26px;text-align:center;line-height:48px}
.arrow{position:absolute;width:52px;height:52px;border-radius:50%;background:var(--white);top:234px;display:flex;align-items:center;justify-content:center}

/* projects */
.projects-title{top:2130px;left:0;width:1200px}
.projects-grid{top:2220px;left:106px;width:1004px;height:336px}
.btn{display:block;border:2px solid var(--orange);color:var(--orange);font-size:14px;font-weight:700;letter-spacing:1px;text-align:center}
.btn-more{top:2622px;left:498px;width:202px;height:46px;line-height:42px}

/* testimonials */
.testimonials{top:2763px;left:0;width:1200px;height:382px;background:var(--blue)}
.testimonials h2{color:var(--white);position:absolute;top:64px;width:100%}
.quote{position:absolute;top:148px;width:330px;color:var(--white)}
.avatar{position:absolute;left:0;top:0;width:66px;height:66px;border-radius:50%;background:#e6d3c4;border:3px solid var(--white)}
.quote-body{margin-left:88px;font-size:12px;line-height:18px}
.quote-body .name{margin-top:12px;font-size:10px;font-weight:700;text-transform:uppercase}
.quote-body .role{font-size:10px}
.stars{color:#f3c633;font-size:20px;letter-spacing:3px;margin-top:18px}
.t-arrow{position:absolute;top:176px;width:34px;height:34px;border-radius:50%;border:2px solid var(--white);color:var(--white);text-align:center;line-height:30px;font-size:18px}

/* blog */
.blog-title{top:3236px;left:0;width:1200px}
.post{position:absolute;top:3322px;width:324px}
.post .photo{height:212px;position:relative}
.date{position:absolute;left:0;bottom:0;width:48px;height:70px;background:var(--orange);color:var(--white);text-align:center;font-family:'Josefin Sans',sans-serif}
.date b{display:block;font-size:28px;padding-top:10px}
.date small{font-size:12px}
.post h4{font-family:'Lato',sans-serif;font-size:20px;color:var(--dark);margin-top:30px;line-height:24px}
.post p{font-size:13px;line-height:20px;margin-top:14px;color:var(--muted)}
.post .author{border-top:1px solid var(--line);margin-top:18px;padding-top:14px;font-size:12px;display:flex;gap:6px;align-items:center}

/* contact */
.contact{top:3800px;left:0;width:1200px;height:444px;background:linear-gradient(#6f6f6f,#3d3d3d)}
.contact h2{color:var(--white);position:absolute;top:60px;width:100%}
.field{position:absolute;background:var(--white);font-size:13px;color:var(--muted);padding:10px 14px}
.btn-contact{position:absolute;top:336px;left:530px;width:140px;height:48px;background:var(--orange);color:var(--white);border:none;line-height:48px}

/* footer */
.footer-info{top:4316px;left:240px;width:720px;display:flex;justify-content:space-between;font-size:13px;color:var(--text);align-items:center}
.footer-info div{display:flex;gap:16px;align-items:center}
.ic{width:52px;height:52px;border-radius:50%;border:1px solid var(--line);display:flex;align-items:center;justify-content:center}
.footer-nav{top:4398px;left:0;width:1200px;text-align:center;font-size:15px;color:var(--dark)}
.footer-nav span{margin:0 14px}
.rule{top:4452px;left:100px;width:1000px;height:1px;background:var(--line)}
.copy{top:4478px;left:100px;font-size:12px;color:var(--text)}
.social{top:4470px;left:960px;display:flex;gap:10px}
.social i{width:28px;height:28px;border-radius:50%;border:1px solid var(--orange)}
</style>
</head>
<body>

<header class="site-header">
  <div class="brand"><span class="brand-dot"></span><span class="brand-name">Ridgeline Interiors</span></div>
  <div class="topbar">
    <span><svg width="14" height="14" viewBox="0 0 24 24"><path fill="#e07a1f" d="M6.6 10.8a15 15 0 006.6 6.6l2.2-2.2a1 1 0 011-.25 11.4 11.4 0 003.6.57 1 1 0 011 1V20a1 1 0 01-1 1A17 17 0 013 4a1 1 0 011-1h3.5a1 1 0 011 1c0 1.25.2 2.45.57 3.6a1 1 0 01-.25 1z"/></svg>1 555 010 0199</span>
    <span><svg width="16" height="12" viewBox="0 0 16 12"><rect width="16" height="12" rx="1" fill="#e07a1f"/><path d="M1 1l7 5 7-5" stroke="#fff" fill="none"/></svg>hello@ridgelineinteriors.com</span>
  </div>
  <nav class="nav">
    <span class="active">HOME</span><span>ABOUT US</span><span>SERVICES</span><span>PROJECTS</span><span>BLOG</span><span>CONTACT US</span>
    <svg width="16" height="16" viewBox="0 0 16 16"><circle cx="6.5" cy="6.5" r="5" stroke="#222" stroke-width="2" fill="none"/><path d="M10 10l5 5" stroke="#222" stroke-width="2"/></svg>
  </nav>
</header>

<section class="hero">
  <div class="photo" role="img" aria-label="Bright modern bathroom with freestanding tub and wood vanities" style="position:absolute;inset:0"></div>
  <div class="hero-band">
    <h1>Ridgeline Interiors</h1>
    <p>Interior business &amp; new construction company</p>
  </div>
  <div class="dots"><i></i><i></i><i></i><i></i></div>
</section>

<h2 class="abs welcome-title">Welcome to Ridgeline Interiors</h2>
<p class="abs welcome-text">Nam libero tempore, cum soluta nobis est eligendi optio cumque nihil impedit quo minus id quod maxime placeat facere possimus, omnis voluptas assumenda est, omnis dolor repellendus et molestiae enim dolor repellendus.</p>

<section class="abs services">
  <div class="photo" role="img" aria-label="Living room corner with purple flowers on a table"></div>
  <div class="tile orange">
    <svg width="80" height="80" viewBox="0 0 80 80"><circle cx="40" cy="30" r="22" fill="#fff"/><rect x="36" y="48" width="8" height="22" fill="#fff"/></svg>
    <h3>Floral Arrangements</h3>
    <p>At vero eos et accusamus et iusto odio dignissimos ducimus qui blanditiis praesenti um voluptatum deleniti atque.</p>
  </div>
  <div class="photo warm" role="img" aria-label="Children's bedroom with built-in bunk and stairs"></div>
  <div class="tile green">
    <svg width="80" height="80" viewBox="0 0 80 80"><line x1="40" y1="4" x2="40" y2="16" stroke="#fff" stroke-width="3"/><circle cx="40" cy="42" r="26" fill="none" stroke="#fff" stroke-width="4"/><path d="M14 42h52M40 16v52M20 28h40M20 56h40" stroke="#fff" stroke-width="3"/></svg>
    <h3>Decorating</h3>
    <p>At vero eos et accusamus et iusto odio dignissimos ducimus qui blanditiis praesenti um voluptatum deleniti atque.</p>
  </div>
  <div class="photo warm" role="img" aria-label="Stone wine cellar with chandelier"></div>
  <div class="tile blue">
    <svg width="80" height="80" viewBox="0 0 80 80"><path d="M50 8l5 12 13 1-10 8 3 13-11-7-11 7 3-13-10-8 13-1z" fill="none" stroke="#fff" stroke-width="3"/><path d="M22 44l3 7 8 1-6 5 2 8-7-4-7 4 2-8-6-5 8-1z" fill="none" stroke="#fff" stroke-width="3"/></svg>
    <h3>Holiday Decorating</h3>
    <p>At vero eos et accusamus et iusto odio dignissimos ducimus qui blanditiis praesenti um voluptatum deleniti atque.</p>
  </div>
</section>

<section class="abs ba">
  <div class="ba-frame">
    <div class="photo" role="img" aria-label="Kitchen before renovation with plain white cabinets"><div class="ba-label">Before</div></div>
    <div class="photo warm" role="img" aria-label="Kitchen after renovation with dark wood cabinets and steel appliances"><div class="ba-label">After</div></div>
  </div>
  <div class="arrow" style="left:72px"><svg width="14" height="20" viewBox="0 0 14 20"><path d="M11 2L3 10l8 8" stroke="#333" stroke-width="3" fill="none"/></svg></div>
  <div class="arrow" style="left:1090px"><svg width="14" height="20" viewBox="0 0 14 20"><path d="M3 2l8 8-8 8" stroke="#333" stroke-width="3" fill="none"/></svg></div>
</section>

<h2 class="abs projects-title">Our Projects</h2>
<div class="abs projects-grid">
  <div class="photo warm abs" role="img" aria-label="Stone house exterior with swimming pool" style="left:0;top:0;width:492px;height:336px"></div>
  <div class="photo warm abs" role="img" aria-label="Open dining area with wooden beams" style="left:506px;top:0;width:240px;height:160px"></div>
  <div class="photo warm abs" role="img" aria-label="Dining room with chandelier" style="left:764px;top:0;width:240px;height:160px"></div>
  <div class="photo abs" role="img" aria-label="White kitchen with island" style="left:506px;top:176px;width:240px;height:160px"></div>
  <div class="photo abs" role="img" aria-label="Bright living room with sofas" style="left:764px;top:176px;width:240px;height:160px"></div>
</div>
<span class="abs btn btn-more">VIEW MORE PROJECTS</span>

<section class="abs testimonials">
  <h2>Client Testimonials</h2>
  <span class="t-arrow" style="left:30px">&#8249;</span>
  <span class="t-arrow" style="left:1134px">&#8250;</span>
  <div class="quote" style="left:100px">
    <div class="avatar" role="img" aria-label="Client portrait"></div>
    <div class="quote-body">&ldquo; At vero eos et accusamus et iusto odio dignissimos ducimus qui blanditiis praesenti um voluptatum deleniti atq.
      <div class="name">Marla Jennings</div><div class="role">Financial Services Professional</div>
      <div class="stars">★★★★☆</div></div>
  </div>
  <div class="quote" style="left:444px">
    <div class="avatar" role="img" aria-label="Client portrait"></div>
    <div class="quote-body">&ldquo; At vero eos et accusamus et iusto odio dignissimos ducimus qui blanditiis praesenti um voluptatum deleniti atq.
      <div class="name">Peter L. Hawthorne</div><div class="role">Regional Home Builder &amp; Partner</div>
      <div class="stars">★★★★☆</div></div>
  </div>
  <div class="quote" style="left:788px">
    <div class="avatar" role="img" aria-label="Client portrait"></div>
    <div class="quote-body">&ldquo; At vero eos et accusamus et iusto odio dignissimos ducimus qui blanditiis praesenti um voluptatum deleniti atq.
      <div class="name">Rosa Delmont</div><div class="role">Creative Strategist | Entrepreneur</div>
      <div class="stars">★★★★☆</div></div>
  </div>
</section>

<h2 class="abs blog-title">Latest Blog</h2>
<article class="post" style="left:98px">
  <div class="photo" role="img" aria-label="Dining room with long pendant light"><div class="date"><b>04</b><small>SEP</small></div></div>
  <h4>At vero eos et accusamus et iustoer odio dignissimos duci</h4>
  <p>At vero eos et accusamus et iusto odio dignissimodu cimus qui blanditiis praesentium volup</p>
  <div class="author"><svg width="10" height="12" viewBox="0 0 10 12"><circle cx="5" cy="3" r="3" fill="#3a9acb"/><path d="M0 12a5 5 0 0110 0z" fill="#3a9acb"/></svg>Nina Castell</div>
</article>
<article class="post" style="left:442px">
  <div class="photo warm" role="img" aria-label="Home basketball court with wood floor"><div class="date"><b>30</b><small>AUG</small></div></div>
  <h4>At vero eos et accusamus et iustoer odio dignissimos duci</h4>
  <p>At vero eos et accusamus et iusto odio dignissimodu cimus qui blanditiis praesentium volup</p>
  <div class="author"><svg width="10" height="12" viewBox="0 0 10 12"><circle cx="5" cy="3" r="3" fill="#3a9acb"/><path d="M0 12a5 5 0 0110 0z" fill="#3a9acb"/></svg>Nina Castell</div>
</article>
<article class="post" style="left:784px">
  <div class="photo warm" role="img" aria-label="Master bedroom with tray ceiling"><div class="date"><b>08</b><small>SEP</small></div></div>
  <h4>At vero eos et accusamus et iustoer odio dignissimos duci</h4>
  <p>At vero eos et accusamus et iusto odio dignissimodu cimus qui blanditiis praesentium volup</p>
  <div class="author"><svg width="10" height="12" viewBox="0 0 10 12"><circle cx="5" cy="3" r="3" fill="#3a9acb"/><path d="M0 12a5 5 0 0110 0z" fill="#3a9acb"/></svg>Nina Castell</div>
</article>

<section class="abs contact" role="img" aria-label="Softly shaded interior doorway behind the contact form">
  <h2>Get In Touch</h2>
  <div class="field" style="left:257px;top:130px;width:338px;height:42px">First Name</div>
  <div class="field" style="left:605px;top:130px;width:338px;height:42px">Last Name</div>
  <div class="field" style="left:257px;top:184px;width:338px;height:42px">Email Address</div>
  <div class="field" style="left:605px;top:184px;width:338px;height:42px">Phone Number</div>
  <div class="field" style="left:257px;top:238px;width:686px;height:82px">Message</div>
  <span class="btn btn-contact">CONTACT US</span>
</section>

<div class="abs footer-info">
  <div><span class="ic"><svg width="16" height="22" viewBox="0 0 16 22"><path d="M8 0a8 8 0 018 8c0 6-8 14-8 14S0 14 0 8a8 8 0 018-8z" fill="#e07a1f"/><circle cx="8" cy="8" r="3" fill="#fff"/></svg></span><span>At vero eos et accu<br>samus et iusto odio dimos duciimu</span></div>
  <div><span class="ic"><svg width="18" height="18" viewBox="0 0 24 24"><path fill="#e07a1f" d="M6.6 10.8a15 15 0 006.6 6.6l2.2-2.2a1 1 0 011-.25 11.4 11.4 0 003.6.57 1 1 0 011 1V20a1 1 0 01-1 1A17 17 0 013 4a1 1 0 011-1h3.5a1 1 0 011 1c0 1.25.2 2.45.57 3.6a1 1 0 01-.25 1z"/></svg></span><span>1 555 010 0199</span></div>
  <div><span class="ic"><svg width="18" height="14" viewBox="0 0 16 12"><rect width="16" height="12" rx="1" fill="#e07a1f"/><path d="M1 1l7 5 7-5" stroke="#fff" fill="none"/></svg></span><span>hello@ridgelineinteriors.com</span></div>
</div>
<div class="abs footer-nav"><span>Home</span>|<span>About Us</span>|<span>Services</span>|<span>Projects</span>|<span>Blog</span>|<span>Contact Us</span></div>
<div class="abs rule"></div>
<div class="abs copy">Copyrights © 2018, Ridgeline Interiors. All rights reserved.</div>
<div class="abs social"><i></i><i></i><i></i><i></i></div>

</body>
</html>
```